Business Card Design Project - del varosi group

dear Sirs

we need business card design for our group ( DEL Varosi Group ) , i have got the Logo design of our group from pixel harbor in previous , so all need details relating to our group i think available with you, as well as the the chosen logo design

we hope to provide us with business card logo that to be appropaite and satisfactory to us .

thanks

note : logo design of our group is attached .
Updates

Reason: please extend the deadline of my project for additional 15 days because i didn't received appropriate design for our gruop yet . kindly beaware that i have received 77 design till now , supossed to send me 200-250 design at least . thanks

Target Market(s)

contents

name : Kerem EL Nadiri

position : Operation Manager

Industry/Entity Type

Business

Requirements
Must have

• person name

group logo
Nice to have
• logo color matching with back background

```html
<!DOCTYPE html>
<html lang="en">
<head>
<meta charset="utf-8">
<title>DEL Varosi Group – Business Card</title>
<link rel="stylesheet" href="https://fonts.googleapis.com/css2?family=Open+Sans:wght@400;600&display=swap">
<style>
  :root {
    --backdrop: #efe6cf;
    --gold-light: #e6b85a;
    --gold-mid: #c9962f;
    --gold-deep: #a87a22;
    --gold-glow: rgba(246, 222, 163, 0.55);
    --gold-text: #d9a63c;
    --navy: #1d4a86;
    --ink: #333333;
    --paper: #ffffff;
  }
  * { margin: 0; padding: 0; box-sizing: border-box; }
  html, body {
    width: 1200px; height: 951px; overflow: hidden;
    background: var(--backdrop);
    font-family: "Open Sans", Arial, sans-serif;
  }
  .stage { position: relative; width: 1200px; height: 951px; }

  .card {
    position: absolute;
    width: 640px; height: 366px;
    border-radius: 22px;
    overflow: hidden;
    box-shadow: 0 10px 26px rgba(80, 60, 20, 0.28);
  }

  /* Front */
  .card-front {
    left: 90px; top: 100px;
    background: linear-gradient(120deg, var(--gold-light) 0%, var(--gold-mid) 55%, var(--gold-deep) 100%);
  }
  .card-front .accent-area {
    position: absolute; right: 0; top: 0;
    width: 380px; height: 170px;
    background: radial-gradient(ellipse at 90% 10%, var(--gold-glow) 0%, rgba(246, 222, 163, 0) 70%);
  }
  .card-front .brand {
    position: absolute; left: 70px; top: 166px;
    display: flex; align-items: center; gap: 16px;
  }
  .brand-mark { width: 22px; height: 22px; background: var(--navy); flex: none; }
  .brand-name {
    font-weight: 600; color: var(--navy);
    letter-spacing: 1px; text-transform: uppercase;
    white-space: nowrap;
  }
  .card-front .brand-name { font-size: 42px; }

  /* Back */
  .card-back {
    left: 470px; top: 470px;
    background: var(--paper);
  }
  .card-back .panel { position: absolute; inset: 0; }
  .card-back .brand {
    position: absolute; left: 36px; top: 38px;
    display: flex; align-items: center; gap: 12px;
  }
  .card-back .brand-mark { width: 16px; height: 16px; }
  .card-back .brand-name { font-size: 23px; }

  .contact {
    position: absolute; left: 40px; top: 120px;
    list-style: none; color: var(--ink);
    font-size: 17px; line-height: 1.3;
  }
  .contact li { display: flex; align-items: flex-start; gap: 10px; margin-bottom: 4px; }
  .contact .icon { width: 16px; height: 16px; flex: none; margin-top: 3px; fill: var(--gold-mid); }
  .contact .domain { color: var(--gold-mid); }

  .person {
    position: absolute; right: 42px; bottom: 38px;
    width: 200px;
  }
  .person-name { color: var(--gold-text); font-size: 20px; font-weight: 400; }
  .person-role { color: var(--paper); font-size: 17px; margin-top: 2px; }
</style>
</head>
<body>
<main class="stage">

  <section class="card card-front" aria-label="Card front">
    <div class="accent-area" role="img" aria-label="Soft light-gold decorative sweep in the upper right corner"></div>
    <div class="brand">
      <span class="brand-mark"></span>
      <span class="brand-name">DEL Varosi Group</span>
    </div>
  </section>

  <section class="card card-back" aria-label="Card back">
    <svg class="panel" viewBox="0 0 640 366" preserveAspectRatio="none" aria-hidden="true">
      <path d="M360,0 C300,110 340,250 290,366 L640,366 L640,0 Z" fill="var(--gold-mid)"/>
      <path d="M385,0 C325,110 365,250 315,366 L640,366 L640,0 Z" fill="var(--navy)"/>
    </svg>

    <div class="brand">
      <span class="brand-mark"></span>
      <span class="brand-name">DEL Varosi Group</span>
    </div>

    <ul class="contact">
      <li>
        <svg class="icon" viewBox="0 0 16 16"><path d="M8 1 L15 8 H13 V15 H9.5 V10.5 H6.5 V15 H3 V8 H1 Z"/></svg>
        <span>1480 Harlow Crest Rd.<br>Suite 204-310<br>Denford, TX 78114</span>
      </li>
      <li>
        <svg class="icon" viewBox="0 0 16 16"><path d="M4 1 L6.5 4.5 L5 6.5 C6 8.5 7.5 10 9.5 11 L11.5 9.5 L15 12 L13 15 C7 14.5 1.5 9 1 3 Z"/></svg>
        <span>512-555-0148</span>
      </li>
      <li>
        <svg class="icon" viewBox="0 0 16 16"><path d="M4 1 H12 V6 H4 Z M1 7 H15 V14 H1 Z M4 10 H12 V12 H4 Z"/></svg>
        <span>512-555-0149</span>
      </li>
      <li>
        <svg class="icon" viewBox="0 0 16 16"><path d="M1 3 H15 V13 H1 Z M1.8 3.8 L8 9 L14.2 3.8" stroke="#fff" stroke-width="1.2"/></svg>
        <span>info@<span class="domain">delvarosigroup</span>.com</span>
      </li>
      <li>
        <svg class="icon" viewBox="0 0 16 16"><circle cx="8" cy="8" r="7"/></svg>
        <span>www.<span class="domain">delvarosigroup</span>.com</span>
      </li>
    </ul>

    <div class="person">
      <p class="person-name">Kerem EL Nadiri</p>
      <p class="person-role">Operation Manager</p>
    </div>
  </section>

</main>
</body>
</html>
```